Request for Business Card Design

Hi. My name is Marlene, I am looking for a new business card design for my company, Quarrow Signal Instruments, LLC. I really like the design you did for Tarsel Venture and was hoping you could do something similar using our full logo and our mark. I am also open to any raised texture design using our mark. I have attached our full logo, which would need to be somewhere on the card, as well as the mark in both outline and full form, as well as our brand colors / guide. The card does not have to be white, as long as our logo and mark appear. I actually like darker colored business cards more, but am open to all options. If you are interested in working with me, please let me know. We would also take the business card design into letterhead design if you can do that.

```html
<!DOCTYPE html>
<html lang="en">
<head>
<meta charset="utf-8">
<title>Quarrow Signal Instruments – Business Card</title>
<link href="https://fonts.googleapis.com/css2?family=Open+Sans:ital,wght@0,400;0,600;0,700;0,800;1,700&display=swap" rel="stylesheet">
<style>
  :root {
    --backdrop: #1c1c1e;
    --card: #ffffff;
    --brand-blue: #0f9abf;
    --ink: #333436;
    --ink-soft: #4a4b4d;
    --ghost: #eef2f6;
  }
  * { box-sizing: border-box; margin: 0; padding: 0; }
  html, body { width: 1200px; height: 900px; overflow: hidden; }
  body {
    background: var(--backdrop);
    font-family: "Open Sans", Arial, sans-serif;
    display: flex;
    flex-direction: column;
    align-items: center;
    justify-content: center;
    gap: 56px;
  }
  .card {
    position: relative;
    width: 580px;
    height: 330px;
    background: var(--card);
    overflow: hidden;
  }
  .card--front { border-bottom: 4px solid var(--brand-blue); }

  /* Wordmark */
  .wordmark { display: flex; flex-direction: column; color: var(--ink); }
  .wordmark__name { font-weight: 800; letter-spacing: 0.06em; line-height: 1; }
  .wordmark__tagline { font-weight: 600; letter-spacing: 0.05em; line-height: 1.2; }

  /* Front side */
  .card--front .wordmark { position: absolute; left: 52px; top: 34px; }
  .card--front .wordmark__name { font-size: 36px; }
  .card--front .wordmark__tagline { font-size: 10.5px; margin-top: 3px; }

  .identity { position: absolute; left: 0; top: 112px; padding-left: 52px; }
  .identity__bar {
    position: absolute; left: 0; top: 2px;
    width: 32px; height: 26px; background: var(--brand-blue);
  }
  .identity__name {
    font-size: 22px; font-weight: 700; font-style: italic;
    color: var(--brand-blue); letter-spacing: 0.03em; text-transform: uppercase;
  }
  .identity__role { font-size: 15px; color: var(--ink-soft); margin-top: -2px; }

  .address { position: absolute; left: 52px; top: 182px; font-size: 14px; color: var(--ink-soft); line-height: 1.45; }

  .contacts { position: absolute; left: 32px; top: 240px; list-style: none; font-size: 14px; color: var(--ink-soft); line-height: 1.5; }
  .contacts li { display: flex; align-items: center; gap: 8px; }
  .contacts svg { width: 13px; height: 13px; fill: var(--brand-blue); flex: none; }

  .front-disc { position: absolute; right: 40px; bottom: 26px; width: 250px; height: 250px; }

  /* Back side */
  .ghost-disc { position: absolute; right: -60px; top: -40px; width: 420px; height: 420px; }
  .card--back .brand-lockup {
    position: absolute; left: 56px; top: 50%; transform: translateY(-50%);
    display: flex; align-items: center; gap: 24px;
  }
  .brand-lockup__dot { width: 96px; height: 96px; border-radius: 50%; background: var(--brand-blue); flex: none; }
  .card--back .wordmark__name { font-size: 48px; }
  .card--back .wordmark__tagline { font-size: 13px; margin-top: 6px; }
</style>
</head>
<body>

  <section class="card card--front" aria-label="Business card front">
    <div class="wordmark">
      <span class="wordmark__name">QUARROW</span>
      <span class="wordmark__tagline">SIGNAL INSTRUMENTS</span>
    </div>

    <div class="identity">
      <span class="identity__bar"></span>
      <p class="identity__name">Owen Castell</p>
      <p class="identity__role">Managing Director</p>
    </div>

    <p class="address">Your address, City<br>State, Zip 1234</p>

    <ul class="contacts">
      <li>
        <svg viewBox="0 0 24 24"><path d="M6.6 10.8a15 15 0 0 0 6.6 6.6l2.2-2.2a1 1 0 0 1 1-.25 11.4 11.4 0 0 0 3.6.57 1 1 0 0 1 1 1V20a1 1 0 0 1-1 1A17 17 0 0 1 3 4a1 1 0 0 1 1-1h3.5a1 1 0 0 1 1 1c0 1.25.2 2.45.57 3.6a1 1 0 0 1-.25 1z"/></svg>
        123 456 789
      </li>
      <li>
        <svg viewBox="0 0 24 24"><path d="M2 5h20v14H2z M2 5l10 8 10-8" fill="none" stroke="currentColor"/><path d="M2 5h20l-10 8z"/><path d="M2 7l10 8 10-8v12H2z"/></svg>
        info@youremail.com
      </li>
      <li>
        <svg viewBox="0 0 24 24"><circle cx="12" cy="12" r="10"/></svg>
        www.yourwebsite.com
      </li>
    </ul>

    <svg class="front-disc" viewBox="0 0 100 100" aria-hidden="true">
      <circle cx="50" cy="50" r="50" fill="var(--brand-blue)"/>
    </svg>
  </section>

  <section class="card card--back" aria-label="Business card back">
    <svg class="ghost-disc" viewBox="0 0 100 100" aria-hidden="true">
      <circle cx="50" cy="50" r="50" fill="var(--ghost)"/>
    </svg>
    <div class="brand-lockup">
      <span class="brand-lockup__dot"></span>
      <div class="wordmark">
        <span class="wordmark__name">QUARROW</span>
        <span class="wordmark__tagline">SIGNAL INSTRUMENTS</span>
      </div>
    </div>
  </section>

</body>
</html>
```